Business card for medical clinic

I need an upmarket, modern medical/health business card for my clinic

Contact Information for Business Card

name, address, email, qr code

```html
<!DOCTYPE html>
<html lang="en">
<head>
<meta charset="utf-8">
<title>Aldera Care Group – Business Card</title>
<link rel="stylesheet" href="https://fonts.googleapis.com/css2?family=Poppins:wght@300;400;500;600&display=swap">
<style>
  :root {
    --stage: #e3e4e6;
    --brand-blue: #22aae2;
    --brand-navy: #1f3d66;
    --ink: #1b1b1b;
    --paper: #ffffff;
    --card-shadow: 0 10px 28px rgba(0, 0, 0, 0.22);
  }
  * { box-sizing: border-box; margin: 0; padding: 0; }
  html, body {
    width: 1200px;
    height: 780px;
    overflow: hidden;
    background: var(--stage);
    font-family: "Poppins", sans-serif;
  }
  .canvas {
    position: relative;
    width: 1200px;
    height: 780px;
    display: flex;
    align-items: center;
    justify-content: center;
    gap: 40px;
  }
  .card {
    position: relative;
    width: 540px;
    height: 309px;
    box-shadow: var(--card-shadow);
    overflow: hidden;
  }

  /* Front */
  .card--front { background: var(--paper); }
  .brand-lockup {
    position: absolute;
    left: 30px;
    top: 112px;
    width: 240px;
    display: flex;
    align-items: center;
    gap: 12px;
  }
  .brand-lockup__dot {
    flex: none;
    width: 38px;
    height: 38px;
    border-radius: 50%;
    border: 3px solid var(--brand-navy);
  }
  .brand-lockup__name {
    font-weight: 500;
    font-size: 21px;
    line-height: 1.15;
    letter-spacing: 0.04em;
    color: var(--brand-navy);
    text-transform: uppercase;
  }
  .divider {
    position: absolute;
    left: 292px;
    top: 46px;
    width: 1px;
    height: 170px;
    background: var(--brand-blue);
  }
  .identity {
    position: absolute;
    left: 318px;
    top: 52px;
  }
  .identity__name {
    font-size: 31px;
    line-height: 1.1;
    color: var(--brand-blue);
    white-space: nowrap;
  }
  .identity__first { font-weight: 600; }
  .identity__last { font-weight: 300; }
  .identity__title {
    font-size: 13px;
    font-weight: 500;
    color: var(--ink);
    margin-top: 2px;
  }
  .contact-list {
    list-style: none;
    margin-top: 16px;
  }
  .contact-list__item {
    display: flex;
    align-items: center;
    gap: 9px;
    font-size: 13px;
    font-weight: 400;
    color: var(--ink);
    line-height: 1.75;
  }
  .contact-list__icon {
    width: 13px;
    height: 13px;
    flex: none;
  }
  .address {
    position: absolute;
    left: 0;
    right: 0;
    bottom: 26px;
    text-align: center;
    font-size: 15px;
    font-weight: 400;
    color: var(--brand-blue);
    letter-spacing: 0.01em;
  }

  /* Back */
  .card--back {
    background: var(--brand-blue);
    display: flex;
    align-items: center;
    justify-content: center;
  }
  .brand-lockup--large {
    position: static;
    width: auto;
    gap: 20px;
  }
  .brand-lockup--large .brand-lockup__dot {
    width: 72px;
    height: 72px;
    border: 4px solid var(--paper);
  }
  .brand-lockup--large .brand-lockup__name {
    color: var(--paper);
    font-size: 34px;
  }
</style>
</head>
<body>
  <main class="canvas">
    <section class="card card--front" aria-label="Business card front">
      <div class="brand-lockup">
        <span class="brand-lockup__dot" aria-hidden="true"></span>
        <span class="brand-lockup__name">Aldera Care Group</span>
      </div>

      <div class="divider" aria-hidden="true"></div>

      <div class="identity">
        <h1 class="identity__name"><span class="identity__first">Marena</span> <span class="identity__last">Koval</span></h1>
        <p class="identity__title">Founder &amp; CEO</p>

        <ul class="contact-list">
          <li class="contact-list__item">
            <svg class="contact-list__icon" viewBox="0 0 24 24" aria-hidden="true">
              <path fill="#22aae2" d="M6.6 10.8a15.2 15.2 0 0 0 6.6 6.6l2.2-2.2c.3-.3.7-.4 1-.2 1.1.4 2.3.6 3.6.6.6 0 1 .4 1 1V20c0 .6-.4 1-1 1C10.6 21 3 13.4 3 4c0-.6.4-1 1-1h3.5c.6 0 1 .4 1 1 0 1.3.2 2.5.6 3.6.1.3 0 .7-.2 1z"/>
            </svg>
            (555) 214-3087
          </li>
          <li class="contact-list__item">
            <svg class="contact-list__icon" viewBox="0 0 24 24" aria-hidden="true">
              <rect x="2" y="5" width="20" height="14" rx="2" fill="#22aae2"/>
              <path d="M3 6.5l9 6.5 9-6.5" fill="none" stroke="#fff" stroke-width="1.8"/>
            </svg>
            hello@alderacare.com
          </li>
          <li class="contact-list__item">
            <svg class="contact-list__icon" viewBox="0 0 24 24" aria-hidden="true">
              <circle cx="12" cy="12" r="10" fill="#22aae2"/>
              <path d="M2 12h20M12 2c3 3 3 17 0 20M12 2c-3 3-3 17 0 20" fill="none" stroke="#fff" stroke-width="1.4"/>
            </svg>
            www.alderacare.com
          </li>
        </ul>
      </div>

      <p class="address">418 Linden Ave. Suite 120 Brookfield, OH 44403</p>
    </section>

    <section class="card card--back" aria-label="Business card back">
      <div class="brand-lockup brand-lockup--large">
        <span class="brand-lockup__dot" aria-hidden="true"></span>
        <span class="brand-lockup__name">Aldera Care Group</span>
      </div>
    </section>
  </main>
</body>
</html>
```